Business card

We need a business card design for our company based in Auckland , New Zealand called 'Ridge + Studio Ltd'. We provide architectural services. We would like to see designs that use the max. three colours (such as white, black, grey) The final design should communicate financial safety and growth."
Also I will provide our company logo. I would like to the logo to be embeded onto our business card.

Target Market(s)

new residential house, alteration & addition & light commericila design & drafting service

Industry/Entity Type

Architecture

Contact Information for Business Card

Company name: ridge + studio Ltd.
Name: Mark Delford
Job title: architectural designer & Design LBP
email address: mark@rplusd.co.nz
mobile number: 02 5163 2290
web site: www.rplusd.co.nz

Requirements
Must have
• My project must have..
• - embeded logo (attached company logo)
• I don't have a bigger version for our company logo, but I have one old one, so you can remove the word from it)
• - insert the attached small BKTW logo & LBP logo
• - creative, simple and clear business card.
• - Max. three colours
Nice to have
• - Here are the samples I would like to share with you: http://www.plimvora.com/blog/minimalistic-business-card-designs/
• I would like to have my business card like one of the creation.
Should not have
• TBA

```html
<!DOCTYPE html>
<html lang="en">
<head>
<meta charset="utf-8">
<title>Ridge + Studio Ltd — Business Card</title>
<link href="https://fonts.googleapis.com/css2?family=Montserrat:wght@300;400;600&family=Roboto+Condensed:wght@700&display=swap" rel="stylesheet">
<style>
  :root {
    --ink: #101012;
    --ink-soft: #2b2b2f;
    --grey: #9a9b9f;
    --grey-light: #b9babd;
    --paper: #ffffff;
    --stage: #e9e8e5;
    --rule: #1d1d24;
    --placeholder: #26262a;
  }
  * { box-sizing: border-box; margin: 0; padding: 0; }
  html, body { width: 1200px; height: 913px; overflow: hidden; }
  body {
    background: var(--stage);
    font-family: "Montserrat", sans-serif;
    position: relative;
  }
  .card {
    position: absolute;
    top: 291px;
    width: 540px;
    height: 330px;
    overflow: hidden;
    box-shadow: 0 10px 30px rgba(0,0,0,.18);
  }

  /* Front */
  .card-front {
    left: 40px;
    background: linear-gradient(160deg, #3a393d 0%, var(--ink) 55%, #050506 100%);
  }
  .front-rule {
    position: absolute;
    left: 0; right: 0;
    top: 226px;
    height: 1.5px;
    background: var(--grey);
  }
  .logo-area {
    position: absolute;
    left: 200px; top: 48px;
    width: 140px; height: 140px;
    background: var(--placeholder);
    border-radius: 6px;
  }
  .name-tab {
    position: absolute;
    left: 95px; top: 208px;
    width: 350px; height: 38px;
    background: var(--grey);
    clip-path: polygon(0 30%, 4% 0, 96% 0, 100% 30%, 100% 70%, 96% 100%, 4% 100%, 0 70%);
    display: flex; align-items: center; justify-content: center;
  }
  .company-name {
    font-family: "Roboto Condensed", sans-serif;
    font-weight: 700;
    font-size: 26px;
    letter-spacing: -.3px;
    color: var(--ink);
    white-space: nowrap;
  }

  /* Back */
  .card-back {
    left: 620px;
    background: var(--paper);
  }
  .contact-panel {
    position: absolute;
    left: 0; top: 0;
    width: 352px; height: 330px;
    background: linear-gradient(180deg, var(--grey-light), var(--grey));
    border-right: 6px solid var(--rule);
  }
  .row {
    position: absolute;
    left: 0;
    background: var(--paper);
    border-top: 6px solid var(--rule);
    border-bottom: 6px solid var(--rule);
    border-right: 6px solid var(--rule);
    display: flex; flex-direction: column; justify-content: center; align-items: flex-end;
    padding-right: 16px;
    white-space: nowrap;
  }
  .row-name { top: 22px; width: 322px; height: 92px; }
  .row-phone { top: 120px; width: 272px; height: 58px; }
  .row-web { top: 184px; width: 286px; height: 58px; }
  .row-mail { top: 248px; width: 300px; height: 58px; }
  .person {
    font-size: 28px; font-weight: 300; letter-spacing: .5px; color: var(--ink); line-height: 1.1;
  }
  .person strong { font-weight: 600; }
  .role { font-size: 14px; font-weight: 400; color: var(--ink-soft); margin-top: 4px; }
  .detail { font-size: 17px; font-weight: 400; color: var(--ink); }
  .icon-box {
    position: absolute;
    width: 34px; height: 34px;
    background: var(--grey);
    border: 3px solid var(--rule);
    display: flex; align-items: center; justify-content: center;
  }
  .icon-phone { left: 282px; top: 132px; }
  .icon-web { left: 296px; top: 196px; }
  .icon-mail { left: 310px; top: 260px; }
  .credentials {
    position: absolute;
    left: 390px; top: 50px;
    display: flex; flex-direction: column; align-items: center; gap: 36px;
  }
  .badge-round {
    width: 78px; height: 78px; border-radius: 50%;
    background: var(--ink-soft);
  }
  .badge-plate {
    width: 100px; height: 44px; border-radius: 4px;
    background: var(--grey);
  }
</style>
</head>
<body>
  <section class="card card-front" aria-label="Card front">
    <div class="logo-area" role="img" aria-label="Company logo"></div>
    <div class="front-rule"></div>
    <div class="name-tab"><span class="company-name">ridge + studio Ltd.</span></div>
  </section>

  <section class="card card-back" aria-label="Card back">
    <div class="contact-panel"></div>
    <div class="row row-name">
      <p class="person">MARK <strong>DELFORD</strong></p>
      <p class="role">Architectural Designer &amp; Design LBP</p>
    </div>
    <div class="row row-phone"><p class="detail">02 5163 2290</p></div>
    <div class="row row-web"><p class="detail">www.rplusd.co.nz</p></div>
    <div class="row row-mail"><p class="detail">mark@rplusd.co.nz</p></div>

    <div class="icon-box icon-phone">
      <svg width="16" height="18" viewBox="0 0 16 18"><rect x="3" y="1" width="10" height="16" rx="2" fill="none" stroke="#fff" stroke-width="2"/><circle cx="8" cy="14" r="1" fill="#fff"/></svg>
    </div>
    <div class="icon-box icon-web">
      <svg width="18" height="18" viewBox="0 0 18 18" fill="none" stroke="#fff" stroke-width="1.6"><circle cx="9" cy="9" r="7.5"/><ellipse cx="9" cy="9" rx="3.2" ry="7.5"/><line x1="1.5" y1="9" x2="16.5" y2="9"/></svg>
    </div>
    <div class="icon-box icon-mail">
      <svg width="18" height="14" viewBox="0 0 18 14" fill="none" stroke="#fff" stroke-width="1.6"><rect x="1" y="1" width="16" height="12"/><polyline points="1,1 9,8 17,1"/></svg>
    </div>

    <div class="credentials">
      <div class="badge-round" role="img" aria-label="Licensed practitioner badge"></div>
      <div class="badge-plate" role="img" aria-label="BKTW professional member badge"></div>
    </div>
  </section>
</body>
</html>
```